Road Construction Company needs business cards

We would like a new business card designed for our business.

We're a road construction company based in Qld, Australia.

Can the business card please have the following information on it.

Name: Warren Halbeck
Position: General Manager
Phone: 0472 915 348
Email: Warren.halbeck@tovrin.com.au
Address: 87 Marrow Ave, Pendlebay, QLD, 4023
Website: www.tovrin.com.au

Visually we'd like the card to be professional and simple.

Attached is our logo.

Our website is www.tovrin.com.au

Target Market(s)

Men aged 25-60

Contact Information for Business Card

As listed in project description

Font styles to use
Serif

Requirements
Must have
• Large logo on back of card

```html
<!DOCTYPE html>
<html lang="en">
<head>
<meta charset="utf-8">
<title>Tovrin Road Construction – Business Card</title>
<link href="https://fonts.googleapis.com/css2?family=Exo+2:wght@400;500;800&display=swap" rel="stylesheet">
<style>
  :root {
    --backdrop: #1f1f20;
    --brand-blue: #0453a5;
    --accent-blue: #35a4d8;
    --paper: #ffffff;
    --ink-light: #ffffff;
  }
  * { box-sizing: border-box; margin: 0; padding: 0; }
  html, body {
    width: 1200px; height: 1015px; overflow: hidden;
    background: var(--backdrop);
    font-family: "Exo 2", sans-serif;
  }
  .canvas {
    position: relative; width: 1200px; height: 1015px;
  }
  .card {
    position: absolute; left: 280px;
    width: 640px; height: 366px;
    overflow: hidden;
    box-shadow: 0 14px 30px rgba(0,0,0,.55);
  }
  .card--front { top: 100px; background: var(--brand-blue); }
  .card--back { top: 548px; background: var(--paper); }

  .wordmark {
    font-weight: 800; text-transform: uppercase;
    letter-spacing: 2px; line-height: 1;
  }
  .card--front .wordmark {
    position: absolute; left: 0; right: 0; top: 108px;
    text-align: center; font-size: 72px; color: var(--ink-light);
  }
  .web-band {
    position: absolute; left: 0; right: 0; top: 240px; height: 34px;
    background: var(--accent-blue);
    display: flex; align-items: center; justify-content: center;
    color: var(--ink-light); font-size: 17px; font-weight: 500; letter-spacing: 2px;
  }

  .panel-shape { position: absolute; inset: 0; }
  .card--back .wordmark {
    position: absolute; left: 0; width: 320px; top: 176px;
    text-align: center; font-size: 52px; color: var(--brand-blue);
  }
  .contact {
    position: absolute; left: 352px; top: 104px; right: 16px;
    color: var(--ink-light);
  }
  .contact__name {
    font-weight: 800; text-transform: uppercase; color: var(--accent-blue);
    font-size: 21px; letter-spacing: 1px; line-height: 1;
  }
  .contact__role { font-size: 16px; margin-top: 3px; }
  .contact__lines { list-style: none; margin-top: 14px; font-size: 15px; line-height: 1.35; }
  .contact__lines li { display: flex; align-items: center; gap: 7px; }
  .contact__lines svg { width: 13px; height: 13px; flex: none; }
  .contact__address { margin-top: 14px; font-size: 15px; line-height: 1.35; font-style: normal; }
</style>
</head>
<body>
<main class="canvas">
  <section class="card card--front" aria-label="Card front">
    <div class="wordmark">Tovrin</div>
    <div class="web-band">www.tovrin.com.au</div>
  </section>

  <section class="card card--back" aria-label="Card back">
    <svg class="panel-shape" viewBox="0 0 640 366" aria-hidden="true">
      <polygon points="320,0 640,0 640,366 320,366" fill="var(--brand-blue)"/>
      <line x1="320" y1="0" x2="320" y2="366" stroke="var(--accent-blue)" stroke-width="5"/>
      <polygon points="318,138 338,148 318,158" fill="var(--accent-blue)"/>
    </svg>
    <div class="wordmark">Tovrin</div>
    <div class="contact">
      <div class="contact__name">Warren Halbeck</div>
      <div class="contact__role">General Manager</div>
      <ul class="contact__lines">
        <li>
          <svg viewBox="0 0 16 16" aria-hidden="true"><path d="M4 1.5l2.5 3-1.5 1.8c.8 1.7 2.2 3.1 3.9 3.9L10.7 8.7l3 2.5-1.6 2.8C7 13.6 2.4 9 2 3.2z" fill="var(--accent-blue)"/></svg>
          0472 915 348
        </li>
        <li>
          <svg viewBox="0 0 16 16" aria-hidden="true"><rect x="1" y="3" width="14" height="10" fill="var(--accent-blue)"/><path d="M1 3l7 6 7-6" fill="none" stroke="var(--brand-blue)" stroke-width="1.4"/></svg>
          Warren.halbeck@tovrin.com.au
        </li>
      </ul>
      <address class="contact__address">87 Marrow Ave<br>Pendlebay, QLD, 4023</address>
    </div>
  </section>
</main>
</body>
</html>
```